Corvana Tongue Works, LLC

We need a business card that includes information about our business and conveys a reliable business that provides document translation services and interpreters for a variety of corporate and individual clients. We want to come across as professional, reliable, yet approachable. It should include the following on one side:

ESL / ENL Language Classes, Private Lessons, and Online Tutors
PLEXA Training and Testing
Translating & Interpreting Services
Contact us about Over-the-Phone Interpreting in over 200 languages
24/7/365
www.corvanatongue.example

The other side should include (555) 481-3062

Rhoda Pelling, President
482 Garnet Ave., Ste. 219
Indianapolis, IN 40917

Please add USA as part of the address. Also, please add rmpelling@corvanatongueworks.example as the e-mail address. Thank you.

Target Market(s)

Business professionals, their families, the international community

Industry/Entity Type

Business

Contact Information for Business Card

24/7/365
www.corvanatongue.example

(555) 481-3062

Rhoda Pelling, President
482 Garnet Ave., Ste. 219
Indianapolis, IN 40917
USA

Font styles to use
Sans Serif

Colors

Designer to choose colors to be used in the design.

Requirements
Must have
• See project description
• e-mail address and web address
• Phone number
Nice to have
• a globe
• physical address
Should not have
• Should not have the same color scheme as other agencies in our market in Indiana unless it is blue and black. No purple or yellow.

```html
<!DOCTYPE html>
<html lang="en">
<head>
<meta charset="utf-8">
<title>Corvana Tongue Works – Business Card</title>
<link rel="stylesheet" href="https://fonts.googleapis.com/css2?family=Lato:wght@400;700;900&display=swap">
<style>
  :root {
    --brand-blue: #2a93d0;
    --ink: #1c1c1c;
    --card-white: #f7f7f7;
    --paper-bg: #e6e4e1;
    --map-tone: #e3e3e3;
    --white: #ffffff;
  }
  * { margin: 0; padding: 0; box-sizing: border-box; }
  html, body {
    width: 1200px; height: 960px; overflow: hidden;
    background: var(--paper-bg);
    font-family: "Lato", Arial, sans-serif;
  }
  .stage { position: relative; width: 1200px; height: 960px; }

  .card {
    position: absolute; width: 600px; height: 342px;
    border-radius: 18px; overflow: hidden;
    box-shadow: 0 4px 10px rgba(0,0,0,.35);
  }
  .card--front { left: 302px; top: 128px; background: #000; }
  .card--back  { left: 299px; top: 488px; background: var(--card-white); }

  .front-art { position: absolute; inset: 0; }

  .front-company {
    position: absolute; left: 31px; top: 26px;
    color: var(--white); font-size: 35px; line-height: 40px; font-weight: 400;
  }
  .front-company .llc { font-size: 15px; }
  .front-person { position: absolute; left: 32px; top: 156px; color: var(--white); }
  .front-person .name { font-size: 21px; font-weight: 700; letter-spacing: .2px; }
  .front-person .role { font-size: 15px; font-weight: 700; margin-left: 1px; margin-top: 1px; }
  .front-address {
    position: absolute; left: 32px; top: 204px;
    color: var(--white); font-size: 15px; line-height: 18px; font-style: normal;
  }
  .front-contacts {
    position: absolute; left: 32px; top: 263px;
    list-style: none; color: var(--white); font-size: 13.5px; line-height: 19px;
  }
  .front-contacts li { display: flex; align-items: center; gap: 8px; }
  .front-contacts svg { width: 13px; height: 13px; fill: var(--white); flex: none; }

  .front-mark-name {
    position: absolute; left: 275px; top: 146px; width: 318px;
    text-align: center; color: var(--brand-blue);
    font-size: 50px; font-weight: 700; line-height: 52px;
  }

  .back-map {
    position: absolute; left: 0; top: 20px; width: 600px; height: 300px;
    background: radial-gradient(ellipse at center, var(--map-tone) 0%, var(--card-white) 75%);
  }
  .back-brand {
    position: absolute; left: 186px; top: 43px;
    display: flex; align-items: center; gap: 10px;
  }
  .back-brand .dot {
    width: 94px; height: 94px; border-radius: 50%; background: var(--brand-blue);
  }
  .back-brand .name {
    color: var(--ink); font-size: 25px; line-height: 28px; font-weight: 400;
  }
  .back-brand .name small { font-size: 11px; }

  .back-services {
    position: absolute; left: 0; top: 152px; width: 600px;
    text-align: center; color: var(--ink); font-size: 14.5px; line-height: 19px;
  }
  .back-services .bullet {
    display: inline-block; width: 5px; height: 5px; border-radius: 50%;
    background: var(--brand-blue); vertical-align: middle; margin: 0 2px;
  }
  .back-phone-note {
    position: absolute; left: 0; top: 199px; width: 600px;
    text-align: center; color: var(--ink); font-size: 15.5px; line-height: 19px; font-weight: 700;
  }
  .back-hours {
    position: absolute; left: 0; top: 250px; width: 600px;
    display: flex; justify-content: center; align-items: center; gap: 5px;
    color: var(--ink); font-size: 21px; font-weight: 900;
  }
  .back-hours svg { width: 19px; height: 19px; }
  .back-web {
    position: absolute; left: 0; top: 279px; width: 600px;
    text-align: center; color: var(--brand-blue); font-size: 17px;
  }
  .back-web strong { font-weight: 900; }
</style>
</head>
<body>
<main class="stage">

  <section class="card card--front" aria-label="Card front">
    <svg class="front-art" viewBox="0 0 600 342" aria-hidden="true">
      <rect x="0" y="0" width="433" height="342" fill="var(--brand-blue)"/>
      <circle cx="433" cy="172" r="188" fill="var(--brand-blue)"/>
      <circle cx="433" cy="172" r="160" fill="var(--white)"/>
    </svg>

    <h1 class="front-company">Corvana<br>Tongue<br>Works <span class="llc">LLC</span></h1>

    <div class="front-person">
      <p class="name">RHODA PELLING</p>
      <p class="role">PRESIDENT</p>
    </div>

    <address class="front-address">482 Garnet Ave., Ste. 219<br>Indianapolis, IN 40917<br>USA</address>

    <ul class="front-contacts">
      <li>
        <svg viewBox="0 0 24 24"><path d="M6.6 10.8a15.1 15.1 0 0 0 6.6 6.6l2.2-2.2c.3-.3.7-.4 1-.2 1.1.4 2.3.6 3.6.6.6 0 1 .4 1 1V20c0 .6-.4 1-1 1C10.6 21 3 13.4 3 4c0-.6.4-1 1-1h3.5c.6 0 1 .4 1 1 0 1.3.2 2.5.6 3.6.1.3 0 .7-.2 1z"/></svg>
        (555) 481-3062
      </li>
      <li>
        <svg viewBox="0 0 24 24"><path d="M2 5h20v14H2V5zm2 2v.5l8 5 8-5V7H4z"/></svg>
        rmpelling@corvanatongueworks.example
      </li>
      <li>
        <svg viewBox="0 0 24 24"><path d="M12 2a10 10 0 1 0 0 20 10 10 0 0 0 0-20zm6.9 6h-3a15 15 0 0 0-1.3-3.9A8 8 0 0 1 18.9 8zM12 4c.8 1.2 1.5 2.5 1.9 4h-3.8c.4-1.5 1.1-2.8 1.9-4zM4.3 14a8 8 0 0 1 0-4h3.4a16 16 0 0 0 0 4H4.3zm.8 2h3a15 15 0 0 0 1.3 3.9A8 8 0 0 1 5.1 16zm3-8h-3a8 8 0 0 1 4.3-3.9C8.8 5.3 8.4 6.6 8.1 8zM12 20c-.8-1.2-1.5-2.5-1.9-4h3.8c-.4 1.5-1.1 2.8-1.9 4zm2.3-6H9.7a14 14 0 0 1 0-4h4.6a14 14 0 0 1 0 4zm.3 5.9c.6-1.2 1-2.5 1.3-3.9h3a8 8 0 0 1-4.3 3.9zm1.7-5.9a16 16 0 0 0 0-4h3.4a8 8 0 0 1 0 4h-3.4z"/></svg>
        www.corvanatongue.example
      </li>
    </ul>

    <p class="front-mark-name">Corvana</p>
  </section>

  <section class="card card--back" aria-label="Card back">
    <div class="back-map" role="img" aria-label="Faint world map in light grey behind the text"></div>

    <div class="back-brand">
      <span class="dot" aria-hidden="true"></span>
      <p class="name">Corvana<br>Tongue<br>Works <small>LLC</small></p>
    </div>

    <p class="back-services">
      ESL / ENL Language Classes, Private Lessons, &amp; Online Tutors<br>
      PLEXA Training &amp; Testing <span class="bullet"></span> Translating &amp; Interpreting Services
    </p>

    <p class="back-phone-note">Contact us about Over-the-Phone<br>Interpreting in over 200 languages</p>

    <p class="back-hours">
      <svg viewBox="0 0 24 24" aria-hidden="true"><circle cx="12" cy="12" r="10" fill="none" stroke="var(--ink)" stroke-width="2"/><path d="M12 6v6l-3 4" fill="none" stroke="var(--ink)" stroke-width="2" stroke-linecap="round"/></svg>
      24/7/365
    </p>

    <p class="back-web">www.<strong>CORVANATONGUE</strong>.example</p>
  </section>

</main>
</body>
</html>
```